Modern card design needed for building development company

We are looking for a sharp modern new look for our business cards.
We are a New Zealand based company called TKR Ventures NZ LTD that specialises in subdividing large sections, housing and commercial buildings.
We have attached a photo of the current logo and would like to see it improved somehow as it looks a bit dated.
We are open to any colours.

Target Market(s)

Investors, Property buyers

Industry/Entity Type

Investment

Contact Information for Business Card

TKR VENTURES NZ LTD
www.tkrventuresnz.co.nz

Damon Whitcombe
Phone +64 21 938 104
Email dpwhitcombe@korumail.co.nz

Font styles to use
Serif
Sans Serif

Colors
0792cd
33a6d7
85cae6
6b449b
886aae
f04a50
ec1f27
f37122
f68d4d

Requirements
Must have
• Please try and make the logo more modern or if you have a similar one we would like to see it.

```html
<!DOCTYPE html>
<html lang="en">
<head>
<meta charset="utf-8">
<title>TKR Ventures NZ LTD — Business Card</title>
<link rel="stylesheet" href="https://fonts.googleapis.com/css2?family=Source+Sans+3:wght@400;600;700&display=swap">
<style>
  :root {
    --stage: #000000;
    --card: #2f3033;
    --card-edge: #37383b;
    --accent-green: #5ab82a;
    --text-light: #e6e6e6;
    --divider: #45464a;
    --brand-mark: #e8e8e8;
  }
  * { margin: 0; padding: 0; box-sizing: border-box; }
  html, body {
    width: 1200px; height: 900px; overflow: hidden;
    background: var(--stage);
    font-family: "Source Sans 3", Arial, sans-serif;
  }
  .stage { position: relative; width: 1200px; height: 900px; }
  .card {
    position: absolute; top: 271px;
    width: 457px; height: 281px;
    border-radius: 14px;
    background: var(--card);
    box-shadow: inset 0 0 0 1px var(--card-edge);
  }
  .card--front { left: 137px; }
  .card--back { left: 626px; }

  .brand {
    position: absolute;
    display: flex; align-items: center; gap: 8px;
    color: var(--brand-mark);
    font-weight: 600;
    white-space: nowrap;
  }
  .brand__square {
    width: 12px; height: 12px; background: var(--accent-green);
    flex: none;
  }
  .card--front .brand {
    left: 32px; top: 128px; font-size: 19px; letter-spacing: 0.3px;
  }
  .card--back .brand {
    left: 0; right: 0; justify-content: center;
    top: 124px; font-size: 27px; letter-spacing: 0.5px;
  }

  .divider {
    position: absolute; left: 236px; top: 74px;
    width: 1px; height: 126px; background: var(--divider);
  }
  .holder {
    position: absolute; left: 251px; top: 90px;
    color: var(--accent-green);
    font-weight: 700; font-size: 17px;
  }
  .contact-list {
    position: absolute; left: 251px; top: 133px;
    list-style: none;
  }
  .contact-list li {
    display: flex; align-items: center; gap: 7px;
    height: 19px;
    color: var(--text-light); font-size: 13px;
  }
  .contact-list svg { width: 9px; height: 9px; flex: none; fill: var(--accent-green); }
</style>
</head>
<body>
<main class="stage">
  <section class="card card--front">
    <div class="brand"><span class="brand__square"></span>TKR Ventures NZ LTD</div>
    <div class="divider"></div>
    <h1 class="holder">Damon Whitcombe</h1>
    <ul class="contact-list">
      <li>
        <svg viewBox="0 0 10 10" aria-hidden="true"><path d="M2 0.5 L3.6 2.6 L2.8 3.8 Q4 6 6.2 7.2 L7.4 6.4 L9.5 8 L8.4 9.5 Q2.5 9 0.5 1.6 Z"/></svg>
        +64 21 938 104
      </li>
      <li>
        <svg viewBox="0 0 10 10" aria-hidden="true"><path d="M0.5 2 H9.5 V8.5 H0.5 Z M1.2 2.6 L5 5.4 L8.8 2.6" stroke="#2f3033" stroke-width="0.8"/></svg>
        dpwhitcombe@korumail.co.nz
      </li>
      <li>
        <svg viewBox="0 0 10 10" aria-hidden="true"><circle cx="5" cy="5" r="4.6"/><path d="M0.6 5 H9.4 M5 0.4 Q2.4 5 5 9.6 M5 0.4 Q7.6 5 5 9.6" stroke="#2f3033" stroke-width="0.7" fill="none"/></svg>
        www.tkrventuresnz.co.nz
      </li>
    </ul>
  </section>

  <section class="card card--back">
    <div class="brand"><span class="brand__square"></span>TKR Ventures NZ LTD</div>
  </section>
</main>
</body>
</html>
```